uk based ecommerce website requires fresh look ,high quality look and feel

we are a web based company selling eco friendly ground reinforcement grids to diy and construction sectors
our existing website is www.pondermeshpaths.co.uk ,

we have already updated the logo so that is the branding sorted .so we need a ecommerce website that is very much up-to date in design and layout and which has content management system for ease of use so that we can add products and information as required.

Use current logo as reference for colour scheme.
www.pondermeshpaths.co.uk

The current website has 6 pages accessible through the navigation bar, I would now like 5 pages, removing the need for the Trade Enquiries page possibly have it with along with contact us.

Target Market(s)

construction industry , diy end users,
retail market, landscapers, gardeners

Industry/Entity Type

Construction

Font styles to use
Other font styles liked:
• logo font prometo

Colors
f78f20
9bcb3c

Requirements
Must have
• logo colours and logo design in website with cms responsive design for tablet and mobile devices
• expect content to work flawlessly and look great across all devices
• HTML 5 custom design with coding as required
• must have good experiance in ecommerce website design
• eye catching, high quality look and feel and very user friedly ,very up-to date.
Nice to have
• picture slider show
• explain in writing what exactly i am getting in my ecommerce website
Should not have
• plain , basic design , old fashion looking ,cheap look

```html
<!DOCTYPE html>
<html lang="en">
<head>
<meta charset="utf-8">
<title>Pondermesh Ground Solutions</title>
<link href="https://fonts.googleapis.com/css2?family=Roboto:wght@400;500;700&family=Roboto+Condensed:wght@700&display=swap" rel="stylesheet">
<style>
:root{
  --orange:#f78f20;
  --orange-light:#fbb040;
  --green:#9bcb3c;
  --green-dark:#6fa22a;
  --ink:#222;
  --muted:#666;
  --card:#f4f4f4;
  --nav:#3a3a3a;
  --footer:#222;
  --footer-bottom:#1a1a1a;
  --white:#fff;
}
*{box-sizing:border-box;margin:0;padding:0}
html,body{width:1200px;height:2182px;overflow:hidden;background:var(--white);font-family:'Roboto',Arial,sans-serif;color:var(--ink)}
.wrap{width:1052px;margin:0 auto;position:relative}

.topbar{height:51px;background:linear-gradient(#fba634,var(--orange));color:var(--white);font-size:12px}
.topbar .wrap{display:flex;justify-content:space-between;align-items:center;height:51px}
.topbar .service{font-weight:700;font-size:11px}
.topbar .call{display:flex;align-items:center;gap:8px;font-size:13px}

.header{height:102px}
.header .wrap{display:flex;justify-content:space-between;align-items:center;height:102px}
.brand{display:flex;align-items:center;gap:12px}
.brand-mark{width:40px;height:40px;background:var(--green)}
.brand-name{font-size:22px;font-weight:700;color:var(--orange);letter-spacing:.5px}
.cart{display:flex;align-items:center;gap:12px;font-size:16px}
.cart small{display:block;color:var(--green);font-size:13px}

.nav{height:55px;background:linear-gradient(#4a4a4a,#2f2f2f)}
.nav .wrap{display:flex;height:55px;align-items:stretch}
.nav a{color:var(--white);text-decoration:none;font-size:13px;display:flex;align-items:center;padding:0 31px}
.nav a.active{background:var(--orange);width:107px;justify-content:center;padding:0}
.nav a.nav-products{margin-left:auto;background:var(--green);width:168px;height:55px;justify-content:space-between;padding:0 24px 0 26px}

.hero{height:500px;position:relative;background:linear-gradient(180deg,#55633e 0%,#7a7d72 30%,#8d8b86 60%,#6e6c69 100%)}
.hero h1{position:absolute;top:205px;left:0;right:0;text-align:center;font-family:'Roboto Condensed',Arial,sans-serif;font-size:42px;line-height:50px;color:var(--white);letter-spacing:1px}
.hero h1 span{background:rgba(60,60,60,.55);padding:0 8px}
.arrow{position:absolute;top:210px;width:44px;height:48px;background:rgba(0,0,0,.35);display:flex;align-items:center;justify-content:center}
.arrow.prev{left:0}.arrow.next{right:0}

.intro{text-align:center;padding-top:62px}
.intro h2{font-size:25px;font-weight:500;letter-spacing:.5px}
.intro p{width:820px;margin:18px auto 0;font-size:14px;line-height:21px;color:var(--muted)}

.features{display:flex;justify-content:space-between;margin-top:36px}
.feature{width:512px;height:241px;background:var(--card);display:flex}
.hex{width:240px;height:241px;clip-path:polygon(25% 0,75% 0,100% 50%,75% 100%,25% 100%,0 50%)}
.hex.gravel{background:linear-gradient(#c9c9c4,#6a6a6a 60%,#3d3d3d)}
.hex.grass{background:linear-gradient(#2c3a1e,#4f7a2d 50%,#dcdcdc 80%)}
.feature-body{padding:34px 0 0 20px;width:250px}
.feature-body h3{color:var(--orange);font-size:18px;font-weight:500;line-height:23px}
.feature-body p{margin-top:20px;font-size:13px;line-height:20px;color:var(--muted)}
.btn{display:inline-block;background:var(--orange);color:var(--white);border-radius:20px;font-size:12px;text-decoration:none;text-align:center}
.feature .btn{margin-top:18px;width:124px;line-height:36px}

.product-grid{display:flex;justify-content:space-between;margin-top:39px}
.product{width:243px;height:349px;background:var(--card);text-align:center;box-shadow:0 2px 2px rgba(0,0,0,.06)}
.product .photo{height:186px}
.p1{background:linear-gradient(#b9a78a,#8f7d62 60%,#e6e6e6)}
.p2{background:linear-gradient(#c8ccd0,#7c7f70 45%,#3a3a3a)}
.p3{background:linear-gradient(90deg,#f2f2f2,#d4d4d2 50%,#a9a194)}
.p4{background:linear-gradient(#6f6a62,#3b3834)}
.product h4{color:var(--orange);font-size:16px;font-weight:500;margin-top:22px}
.product p{font-size:14px;line-height:19px;color:var(--muted);margin:8px 26px 0}
.product .btn{margin-top:17px;width:124px;line-height:36px}

.quote{position:absolute;top:1580px;left:0;width:1200px;height:280px;background:radial-gradient(circle at 50% 40%,#9fcf3f,#7fb32e);text-align:center;color:var(--white)}
.quote h5{font-size:21px;font-weight:500;margin-top:68px;letter-spacing:.5px}
.quote .phones{font-size:25px;margin-top:14px;letter-spacing:.5px}
.quote .touch{display:inline-flex;align-items:center;gap:9px;margin-top:26px;background:var(--white);color:var(--ink);border-radius:24px;padding:0 32px;line-height:46px;font-size:13px;font-weight:500;text-decoration:none}

.footer{position:absolute;top:1860px;left:0;width:1200px;height:249px;background:var(--footer);color:#999}
.footer .wrap{display:flex;padding-top:42px}
.footer-brand{width:326px}
.footer-brand .brand-name{color:#e8e8e8;font-size:18px}
.footer-brand .brand-mark{width:30px;height:30px;background:#ccc}
.footer-brand p{margin-top:30px;font-size:12px;line-height:20px;width:260px}
.footer h6{color:var(--white);font-size:16px;font-weight:500;margin-bottom:20px}
.links{width:523px}
.link-cols{display:flex}
.link-cols ul{list-style:none;width:282px}
.link-cols ul+ul{width:200px}
.link-cols li{display:flex;gap:10px;font-size:12px;line-height:18px;margin-bottom:16px}
.link-cols li svg{flex:none;margin-top:2px}
.newsletter input{display:block;width:204px;height:34px;border-radius:17px;border:0;padding:0 22px;font-size:11px;margin-bottom:12px;font-family:inherit}
.newsletter .btn{background:var(--green);width:116px;line-height:34px;margin-left:88px;font-size:13px}

.bottom{position:absolute;top:2109px;left:0;width:1200px;height:73px;background:var(--footer-bottom);color:var(--white);font-size:11px}
.bottom .wrap{display:flex;justify-content:space-between;align-items:center;height:73px}
.bottom b{color:var(--green);font-weight:400}
.cards{display:flex;gap:6px}
.cards span{width:35px;height:22px;border-radius:3px;background:#d8d8d8}
</style>
</head>
<body>

<div class="topbar"><div class="wrap">
  <span class="service">24 HOUR MESSAGING SERVICE</span>
  <span class="call">
    <svg width="18" height="14" viewBox="0 0 18 14"><path d="M1 4q8-6 16 0l-2 3-3-1V4H6v2L3 7z" fill="#fff"/><rect x="4" y="8" width="10" height="5" rx="1" fill="#fff"/></svg>
    Call Us 0142-555-0198 , &nbsp;0845-555-0163
  </span>
</div></div>

<header class="header"><div class="wrap">
  <div class="brand"><span class="brand-mark"></span><span class="brand-name">PONDERMESH</span></div>
  <div class="cart">
    <svg width="44" height="36" viewBox="0 0 44 36"><path d="M2 12h40l-5 21H7z" fill="none" stroke="#222" stroke-width="3"/><path d="M12 12l8-10M32 12l-8-10" stroke="#222" stroke-width="3"/><path d="M14 17v12M22 17v12M30 17v12" stroke="#222" stroke-width="2.5"/></svg>
    <div>Shopping Cart<small>(0)item</small></div>
  </div>
</div></header>

<nav class="nav"><div class="wrap">
  <a class="active" href="#">SHOP</a>
  <a href="#">ABOUT US</a>
  <a href="#">GROUND SOLUTIONS</a>
  <a href="#">CELL</a>
  <a href="#">GRAVEL</a>
  <a href="#">CONTACT US</a>
  <a class="nav-products" href="#">PRODUCTS <svg width="10" height="6"><path d="M0 0h10L5 6z" fill="#fff"/></svg></a>
</div></nav>

<section class="hero" role="img" aria-label="Photo of a gravel path laid over a hexagonal plastic grid beside a brick edge">
  <h1><span>PATHGRID MAKES WALKING</span><br><span>ON IT EASY</span></h1>
  <span class="arrow prev"><svg width="12" height="18"><path d="M10 2 3 9l7 7" stroke="#fff" stroke-width="2.5" fill="none"/></svg></span>
  <span class="arrow next"><svg width="12" height="18"><path d="M2 2l7 7-7 7" stroke="#fff" stroke-width="2.5" fill="none"/></svg></span>
</section>

<main class="wrap">
  <section class="intro">
    <h2>PONDERMESH ECO SOLUTIONS LTD</h2>
    <p>Stabilised Gravel Paving grids combines purpose designed Cellular reinforcement Pavers with the natural appearance, strength, security and free draining characteristics of a loose aggregate surface</p>
  </section>

  <section class="features">
    <article class="feature">
      <div class="hex gravel" role="img" aria-label="Gravel filling a hexagonal driveway grid"></div>
      <div class="feature-body">
        <h3>LIGHT DOMESTIC<br>DRIVEWAYS</h3>
        <p>Neque porro quisquam est qui sit dolorem ipsum quia dolor sit amet, consectetur, adipisci velit</p>
        <a class="btn" href="#">LEARN MORE</a>
      </div>
    </article>
    <article class="feature">
      <div class="hex grass" role="img" aria-label="Grass growing through a reinforcement mesh"></div>
      <div class="feature-body">
        <h3>GRASS REINFORCEMENT<br>MESH AND TURF</h3>
        <p>Neque porro quisquam est qui sit dolorem ipsum quia dolor sit amet, consectetur, adipisci velit</p>
        <a class="btn" href="#">LEARN MORE</a>
      </div>
    </article>
  </section>

  <section class="product-grid">
    <article class="product"><div class="photo p1" role="img" aria-label="Gravel laid on a white parking grid"></div><h4>GRAVEL PARKING</h4><p>Neque porro quisquam est qui sit dolorem ipsum</p><a class="btn" href="#">MORE INFO</a></article>
    <article class="product"><div class="photo p2" role="img" aria-label="Workers laying grid panels on a site with an excavator"></div><h4>GRAVEL PARKING</h4><p>Neque porro quisquam est qui sit dolorem ipsum</p><a class="btn" href="#">MORE INFO</a></article>
    <article class="product"><div class="photo p3" role="img" aria-label="Close view of white hexagon cells beside gravel"></div><h4>GRAVEL PARKING</h4><p>Neque porro quisquam est qui sit dolorem ipsum</p><a class="btn" href="#">MORE INFO</a></article>
    <article class="product"><div class="photo p4" role="img" aria-label="Dark stones filling black hexagon cells"></div><h4>GRAVEL PARKING</h4><p>Neque porro quisquam est qui sit dolorem ipsum</p><a class="btn" href="#">MORE INFO</a></article>
  </section>
</main>

<section class="quote">
  <h5>NEED HELP / ADVICE OR WANT A QUOTE?</h5>
  <p class="phones">CALL US ON: &nbsp;0142-555-0198, &nbsp;0845-555-0163</p>
  <a class="touch" href="#"><svg width="14" height="10"><rect width="14" height="10" fill="#6fa22a"/><path d="M0 0l7 6 7-6" stroke="#fff" fill="none"/></svg>GET IN TOUCH</a>
</section>

<footer class="footer"><div class="wrap">
  <div class="footer-brand">
    <div class="brand"><span class="brand-mark"></span><span class="brand-name">PONDERMESH</span></div>
    <p>Ground Reinforcement Grids Systems For Ground Stabilisation.</p>
  </div>
  <div class="links">
    <h6>LINKS</h6>
    <div class="link-cols">
      <ul>
        <li><svg width="14" height="14"><circle cx="7" cy="7" r="7" fill="#9bcb3c"/><path d="M6 4l3 3-3 3" stroke="#222" stroke-width="1.6" fill="none"/></svg>UK Suppliers Of Ground<br>Reinforcement Systems</li>
        <li><svg width="14" height="14"><circle cx="7" cy="7" r="7" fill="#9bcb3c"/><path d="M6 4l3 3-3 3" stroke="#222" stroke-width="1.6" fill="none"/></svg>Gravel Reinforcement Systems</li>
        <li><svg width="14" height="14"><circle cx="7" cy="7" r="7" fill="#9bcb3c"/><path d="M6 4l3 3-3 3" stroke="#222" stroke-width="1.6" fill="none"/></svg>Grass Reinforcement Systems</li>
      </ul>
      <ul>
        <li><svg width="14" height="14"><circle cx="7" cy="7" r="7" fill="#9bcb3c"/><path d="M6 4l3 3-3 3" stroke="#222" stroke-width="1.6" fill="none"/></svg>Site Map Email</li>
        <li><svg width="14" height="14"><circle cx="7" cy="7" r="7" fill="#9bcb3c"/><path d="M6 4l3 3-3 3" stroke="#222" stroke-width="1.6" fill="none"/></svg>Terms of Service</li>
        <li><svg width="14" height="14"><circle cx="7" cy="7" r="7" fill="#9bcb3c"/><path d="M6 4l3 3-3 3" stroke="#222" stroke-width="1.6" fill="none"/></svg>Delivery and Returns</li>
      </ul>
    </div>
  </div>
  <div class="newsletter">
    <h6>NEWSLETTER</h6>
    <input type="text" placeholder="Enter Name">
    <input type="email" placeholder="Enter Email">
    <a class="btn" href="#">SUBMIT</a>
  </div>
</div></footer>

<div class="bottom"><div class="wrap">
  <span>© 2016 &nbsp;<b>PONDERMESH</b> ECO SOLUTIONS LTD</span>
  <div class="cards"><span></span><span></span><span></span><span></span></div>
</div></div>

</body>
</html>
```